Building company buisness cards

We are looking for a sharp modern new look for our business cards.
We are a New Zealand based company that specialises in house and land packages.
We have attached a photo of the current logo and would like to see if it can be improved somehow if needed.
We are open to any colours but we have chosen green at this stage.
Feel free to change the font and make the logo smarter looking.
Play with the colours and see what looks best.

We want a card that looks so good know one will want to throw it away!

Target Market(s)

Home buyers

Industry/Entity Type

Building

Contact Information for Business Card

Derek Tolvane
0217394062
dtolvane@quillmarkhomesteads.co.nz
quillmarkhomesteads.co.nz

Font styles to use
Serif
Sans Serif

Colors

Designer to choose colors to be used in the design.

Requirements
Must have
• Logo and company name on one side, details on the other side
Nice to have
• Color codes for the original green are HEX #4a8028, RGB(74,128,40), CMYK(42,0,69,50)
• Round corners, Raised and/or spot UV

```html
<!DOCTYPE html>
<html lang="en">
<head>
<meta charset="utf-8">
<title>Quillmark Homesteads business cards</title>
<link rel="stylesheet" href="https://fonts.googleapis.com/css2?family=Arimo:wght@400;700&display=swap">
<style>
  :root {
    --backdrop: #2b2b2d;
    --card: #ffffff;
    --brand-green: #3f9a36;
    --name-blue: #1f6fc4;
    --detail-ink: #2a2a2a;
    --photo-sky: #f3f3ef;
    --photo-house: #d9d2b8;
    --photo-tree: #5f8f3a;
    --photo-hand: #e2b08c;
  }
  * { margin: 0; padding: 0; box-sizing: border-box; }
  html, body { width: 1200px; height: 716px; overflow: hidden; }
  body {
    background: var(--backdrop);
    font-family: "Arimo", Arial, sans-serif;
    position: relative;
  }
  .card {
    position: absolute;
    top: 193px;
    width: 540px;
    height: 330px;
    background: var(--card);
    border-radius: 6px;
    overflow: hidden;
  }
  .card--front { left: 40px; }
  .card--back { left: 620px; }

  .house-photo {
    position: absolute;
    left: 0;
    top: 36px;
    width: 290px;
    height: 250px;
    border-radius: 0 60px 40px 0;
    background:
      radial-gradient(ellipse at 22% 28%, var(--photo-tree) 0 18%, transparent 34%),
      radial-gradient(ellipse at 55% 38%, var(--photo-house) 0 30%, transparent 52%),
      linear-gradient(170deg, var(--photo-sky) 0 55%, var(--photo-hand) 80%, #d49c78 100%);
  }
  .card--back .house-photo { width: 262px; top: 48px; }

  .company-name {
    position: absolute;
    color: var(--brand-green);
    font-weight: 700;
    font-size: 34px;
    line-height: 1.02;
    letter-spacing: -0.5px;
    text-align: center;
  }
  .card--front .company-name { left: 290px; top: 120px; width: 230px; }
  .card--back .company-name { left: 270px; top: 70px; width: 250px; font-size: 32px; }

  .company-mark {
    display: block;
    width: 18px;
    height: 18px;
    margin: 0 auto 8px;
    background: var(--brand-green);
  }

  .contact {
    position: absolute;
    left: 272px;
    top: 166px;
    color: var(--detail-ink);
    font-size: 13px;
    line-height: 21px;
  }
  .contact__name {
    color: var(--name-blue);
    font-size: 19px;
    line-height: 26px;
    margin-bottom: 2px;
  }
  .contact__rule {
    width: 120px;
    height: 1px;
    background: #cfcfcf;
    margin-bottom: 4px;
  }
</style>
</head>
<body>
  <section class="card card--front" aria-label="Card front">
    <div class="house-photo" role="img" aria-label="Photo of an open hand holding a small cream house with a green roof, a tree and a wind turbine, with green leaves drifting"></div>
    <div class="company-name"><span class="company-mark"></span>quillmark<br>homesteads.</div>
  </section>

  <section class="card card--back" aria-label="Card back">
    <div class="house-photo" role="img" aria-label="Photo of an open hand holding a small cream house with a green roof, a tree and a wind turbine, with green leaves drifting"></div>
    <div class="company-name"><span class="company-mark"></span>quillmark<br>homesteads.</div>
    <div class="contact">
      <p class="contact__name">Derek Tolvane</p>
      <div class="contact__rule"></div>
      <p class="contact__phone">0217394062</p>
      <p class="contact__email">dtolvane@quillmarkhomesteads.co.nz</p>
      <p class="contact__web">quillmarkhomesteads.co.nz</p>
    </div>
  </section>
</body>
</html>
```